Laser Tattoo Removal Business Cards

We are looking for a professional business card design for a laser tattoo removal business. Ideally looking for a black business card design. The name of the business is Brightline Tattoo Removal. We place our cards at local tattoo shops so we ideally are looking for something trendy/edgy to draw both male and female clientele in.

Target Market(s)

Male/Female ages 18-60

Contact Information for Business Card

black background ideally.. hoping to stay within greys, whites and black

Font styles to use
Serif
Sans Serif

Colors
121212
a9a9a9
5c5c5c
f5f5f5
ffffff
7f7f7f
606060
848484
9d9d9d

Requirements
Must have
• Employee Info:
• Melissa Thornbury
• Chief Executive Offer
• m: 919.537.2846
• w: 919.362.4178
• f: 919.685.3907
• mthornbury@brightlinetattooremoval.example
• Address:
• 4615 Oakmere Pkwy, Suite 210
• Raleigh, NC 27654
• Website:
• www.brightlinetattooremoval.example
Nice to have
• Myabe business name on back or logo on back and employee info on the front

```html
<!DOCTYPE html>
<html lang="en">
<head>
<meta charset="utf-8">
<title>Brightline Tattoo Removal – Business Cards</title>
<link rel="stylesheet" href="https://fonts.googleapis.com/css2?family=Josefin+Sans:wght@400&family=Roboto:wght@400;500;700&display=swap">
<style>
  :root {
    --stage: #3a3330;
    --card: #121212;
    --ink: #ffffff;
    --soft: #f5f5f5;
    --muted: #a9a9a9;
    --rule: #5c5c5c;
    --band: #ffffff;
    --band-ink: #121212;
  }
  * { margin: 0; padding: 0; box-sizing: border-box; }
  html, body { width: 1200px; height: 769px; overflow: hidden; }
  body {
    background: var(--stage);
    font-family: "Roboto", Arial, sans-serif;
    position: relative;
  }
  .card {
    position: absolute;
    width: 525px;
    height: 300px;
    background: var(--card);
    color: var(--ink);
    overflow: hidden;
    box-shadow: 0 12px 30px rgba(0,0,0,.45);
  }
  .card--front { left: 50px; top: 250px; }
  .card--back  { left: 625px; top: 230px; }

  .wordmark {
    font-family: "Josefin Sans", Arial, sans-serif;
    font-weight: 400;
    color: var(--ink);
    text-align: center;
    text-transform: uppercase;
    letter-spacing: 3px;
    line-height: 1.2;
  }
  .wordmark__name { display: block; font-size: 34px; }
  .wordmark__tag { display: block; font-size: 15px; letter-spacing: 4px; margin-top: 6px; }

  .card--front .wordmark { position: absolute; right: 40px; top: 42px; width: 240px; }

  .person { position: absolute; left: 34px; top: 168px; }
  .person__name { font-size: 17px; font-weight: 700; letter-spacing: .5px; }
  .person__title { font-size: 13px; font-weight: 500; color: var(--soft); margin-top: 2px; }

  .contacts { position: absolute; left: 34px; top: 214px; list-style: none; }
  .contacts li {
    display: flex; align-items: center; gap: 8px;
    font-size: 11.5px; color: var(--soft); height: 15px;
  }
  .contacts svg { width: 11px; height: 11px; fill: var(--ink); flex: none; }

  .divider { position: absolute; left: 300px; top: 214px; width: 1px; height: 56px; background: var(--rule); }
  .address { position: absolute; left: 318px; top: 214px; font-size: 12px; line-height: 16px; color: var(--soft); }

  .card--back .wordmark { position: absolute; left: 0; right: 0; top: 70px; }
  .band {
    position: absolute; left: 0; right: 0; top: 200px; height: 30px;
    background: var(--band); color: var(--band-ink);
    display: flex; align-items: center; justify-content: center;
    font-size: 12px; letter-spacing: 2px;
  }
</style>
</head>
<body>

  <section class="card card--front" aria-label="Business card front">
    <div class="wordmark">
      <span class="wordmark__name">Brightline</span>
      <span class="wordmark__tag">Tattoo Removal</span>
    </div>

    <div class="person">
      <p class="person__name">MELISSA THORNBURY</p>
      <p class="person__title">Chief Executive Offer</p>
    </div>

    <ul class="contacts">
      <li><svg viewBox="0 0 24 24"><path d="M6.6 10.8a15 15 0 0 0 6.6 6.6l2.2-2.2c.3-.3.7-.4 1-.2 1.1.4 2.3.6 3.6.6.6 0 1 .4 1 1V20c0 .6-.4 1-1 1A17 17 0 0 1 3 4c0-.6.4-1 1-1h3.5c.6 0 1 .4 1 1 0 1.3.2 2.5.6 3.6.1.3 0 .7-.2 1z"/></svg>919.362.4178</li>
      <li><svg viewBox="0 0 24 24"><path d="M7 1h10a2 2 0 0 1 2 2v18a2 2 0 0 1-2 2H7a2 2 0 0 1-2-2V3a2 2 0 0 1 2-2zm0 3v14h10V4zm5 15.5a1 1 0 1 0 0 2 1 1 0 0 0 0-2z"/></svg>919.537.2846</li>
      <li><svg viewBox="0 0 24 24"><path d="M6 2h9l3 3v4H6zM3 10h18a1 1 0 0 1 1 1v8a1 1 0 0 1-1 1h-3v2H6v-2H3a1 1 0 0 1-1-1v-8a1 1 0 0 1 1-1zm5 6v4h8v-4z"/></svg>919.685.3907</li>
      <li><svg viewBox="0 0 24 24"><path d="M2 5h20v14H2zm2 2v.5l8 5.5 8-5.5V7l-8 5.5z"/></svg>mthornbury@brightlinetattooremoval.example</li>
      <li><svg viewBox="0 0 24 24"><circle cx="12" cy="12" r="10"/></svg>www.brightlinetattooremoval.example</li>
    </ul>

    <div class="divider"></div>
    <p class="address">4615 Oakmere Pkwy, Suite 210<br>Raleigh, NC 27654</p>
  </section>

  <section class="card card--back" aria-label="Business card back">
    <div class="wordmark">
      <span class="wordmark__name">Brightline</span>
      <span class="wordmark__tag">Tattoo Removal</span>
    </div>
    <div class="band">www.brightlinetattooremoval.example</div>
  </section>

</body>
</html>
```